Talon Microsystems PowerPoint Master Slide Deck Design

This is a 2-phase project to design a slide deck for a semiconductor company in the Silicon Valley. The design budget will be increased with each phase.
The slide deck will need to have one version with a dark background for presentations and a second version with a white background. Otherwise, the slides will be the same. I anticipate we will need a total of 10 slides, but that number may change.
The first phase will be to design a Title and a Title and Content slide.
- The Title Slide is the first slide of the deck. It should include the presentation title, the presenter's name and date of presentation
- The Title and Content slide should include a title and content with bullet points and up to 2 additional sub-bullets
- The Title and Content slide should have a footer that includes the slide #, Talon Microsystems Confidential, and the logo. This footer will be on every slide except the Title Slide
The first two slides will serve as the format for the remaining ~8 slides:
-Header and Content Text (1, 2, 4 column)
-Header and Content Image (bar chart, pie chart, tables)
-Break
-Title only
-Closing (Talon logo only)
Our slides contain a lot of content so a clean and simple design is best.
Both phases will need to include pre-set color options for
-Text and Lines
-Shadows
-Bullets and sub-bullets (including shapes, ex. circle, slash, square, etc.)
-Bar charts, pie charts, tables
Samples of our collateral are attached. Logo files are also attached
Look and feel
Each slider illustrates characteristics of the customer's brand and the style your logo design should communicate.

```html
<!DOCTYPE html>
<html lang="en">
<head>
<meta charset="utf-8">
<title>Talon Microsystems Slide Deck</title>
<link href="https://fonts.googleapis.com/css2?family=Montserrat:wght@400;500;600;700&display=swap" rel="stylesheet">
<style>
  :root {
    --canvas: #e6e6e8;
    --paper: #ffffff;
    --ink: #1e1e24;
    --muted: #55555e;
    --brand: #1414f0;
    --brand-soft: #2a7bf0;
    --link: #2160e8;
    --night: #08080e;
    --bar-1: #2b3a88;
    --bar-2: #2c3385;
    --bar-3: #3b2c87;
    --bar-4: #5c2b84;
    --bar-5: #8d2470;
  }
  * { box-sizing: border-box; margin: 0; padding: 0; }
  html, body { width: 1200px; height: 4202px; overflow: hidden; }
  body { background: var(--canvas); font-family: "Montserrat", sans-serif; color: var(--ink); position: relative; }

  .slide { position: absolute; left: 24px; width: 1152px; height: 649px; background: var(--paper); overflow: hidden; }
  .slide--title { top: 24px; }
  .slide--about { top: 712px; }
  .slide--work { top: 1404px; }
  .slide--chart { top: 2095px; }
  .slide--services { top: 2801px; }
  .slide--closing { top: 3492px; left: 21px; width: 1153px; background: radial-gradient(ellipse at 50% 45%, #15151f 0%, var(--night) 70%); }

  /* Title slide */
  .brand-mark { position: absolute; top: 120px; left: 0; right: 0; display: flex; justify-content: center; align-items: center; gap: 22px; }
  .brand-mark__dot { width: 30px; height: 30px; border-radius: 50%; border: 6px solid var(--brand); }
  .brand-mark__name { font-size: 62px; font-weight: 700; color: var(--ink); letter-spacing: 1px; }
  .slide--closing .brand-mark { top: 288px; }
  .slide--closing .brand-mark__name { color: #ffffff; }

  .title-block { position: absolute; left: 0; right: 0; text-align: center; }
  .title-block__welcome { top: 300px; font-size: 37px; font-weight: 600; }
  .title-block__main { top: 352px; font-size: 60px; font-weight: 700; }
  .title-block__date { top: 450px; font-size: 38px; font-weight: 700; color: var(--brand); }
  .title-block__presenter { top: 540px; font-size: 29px; font-weight: 500; }
  .title-block__presenter span { color: var(--link); }

  /* Header rule */
  .slide-header { position: absolute; top: 18px; left: 0; right: 0; display: flex; align-items: center; height: 40px; }
  .slide-header__line { flex: 1; height: 3px; background: var(--brand); }
  .slide-header__node { width: 22px; height: 22px; border-radius: 50%; border: 3px solid var(--brand); background: var(--paper); flex: none; }
  .slide-header__title { font-size: 38px; font-weight: 700; padding: 0 24px; white-space: nowrap; }

  /* Footer */
  .slide-footer { position: absolute; left: 0; right: 0; bottom: 0; height: 52px; }
  .slide-footer__page { position: absolute; left: 38px; bottom: 8px; font-size: 21px; font-weight: 600; }
  .slide-footer__band { position: absolute; left: 145px; right: 0; top: 0; bottom: 0; background: var(--brand); clip-path: polygon(0 0, 100% 0, 100% 100%, 34px 100%); }
  .slide-footer__accent { position: absolute; left: 141px; top: 0; width: 36px; height: 52px; background: var(--brand-soft); clip-path: polygon(0 0, 8px 0, 38px 100%, 30px 100%); }
  .slide-footer__text { position: absolute; left: 0; right: 0; top: 12px; text-align: center; color: #fff; font-size: 21px; font-weight: 500; }
  .slide-footer__logo { position: absolute; right: 28px; top: 14px; display: flex; align-items: center; gap: 8px; color: #fff; font-size: 17px; font-weight: 600; }
  .slide-footer__logo i { width: 12px; height: 12px; border: 2px solid #fff; border-radius: 50%; display: block; }

  /* Body text */
  .lead { position: absolute; left: 41px; width: 1075px; font-size: 20px; line-height: 33px; font-weight: 500; color: var(--ink); }
  .lead--second { font-size: 18.3px; font-weight: 400; color: var(--muted); }
  .column-text { position: absolute; left: 41px; width: 540px; font-size: 14.6px; line-height: 22.8px; color: var(--muted); }

  .photo-circle { position: absolute; left: 638px; top: 95px; width: 456px; height: 456px; border-radius: 50%; border: 5px solid var(--brand); background: radial-gradient(circle at 40% 35%, #4a9be0 0%, #1a4f9a 45%, #0b1a3a 80%); }

  .bar-chart { position: absolute; left: 620px; top: 80px; }

  /* Services */
  .service { position: absolute; width: 530px; }
  .service__head { display: flex; gap: 10px; font-size: 18.6px; line-height: 24px; font-weight: 500; }
  .service__tick { flex: none; margin-top: 3px; }
  .service__sub { display: flex; gap: 14px; margin-top: 18px; margin-left: 36px; font-size: 11.8px; line-height: 18px; color: var(--muted); }
  .service__ring { flex: none; width: 16px; height: 16px; border-radius: 50%; border: 3.5px solid var(--brand); margin-top: 2px; }
</style>
</head>
<body>

<section class="slide slide--title">
  <div class="brand-mark"><i class="brand-mark__dot"></i><span class="brand-mark__name">Talon Microsystems</span></div>
  <p class="title-block title-block__welcome">Welcome To</p>
  <h1 class="title-block title-block__main">Talon Microsystems</h1>
  <p class="title-block title-block__date">Dec: 12,2023</p>
  <p class="title-block title-block__presenter">The Presenter's Name: <span>Alex Morgan</span></p>
</section>

<section class="slide slide--about">
  <header class="slide-header"><span class="slide-header__line"></span><i class="slide-header__node"></i><h2 class="slide-header__title">About Us</h2><i class="slide-header__node"></i><span class="slide-header__line"></span></header>
  <p class="lead" style="top:100px">Sed ut perspiciatis unde omnis iste natus error sit voluptatem accusantium doloremque laudantium, totam rem aperiam, eaque ipsa quae ab illo inventore veritatis et quasi architecto beatae vitae dicta sunt explicabo. Nemo enim ipsam voluptatem quia voluptas sit aspernatur aut odit aut fugit, sed quia consequuntur magni dolores eos qui ratione voluptatem sequi nesciunt. Neque porro quisquam est, qui dolorem ipsum quia dolor sit amet, consectetur, adipisci velit, sed quia non numquam eius modi tempora incidunt ut labore et dolore magnam aliquam quaerat voluptatem.</p>
  <p class="lead lead--second" style="top:333px">Sed ut perspiciatis unde omnis iste natus error sit voluptatem accusantium doloremque laudantium, totam rem aperiam, eaque ipsa quae ab illo inventore veritatis et quasi architecto beatae vitae dicta sunt explicabo. Nemo enim ipsam voluptatem quia voluptas sit aspernatur aut odit aut fugit, sed quia consequuntur magni dolores eos qui ratione voluptatem sequi nesciunt. Neque porro quisquam est, qui dolorem ipsum quia dolor sit amet, consectetur, adipisci velit, sed quia non numquam eius modi tempora incidunt ut labore et dolore magnam aliquam quaerat voluptatem.</p>
  <footer class="slide-footer"><span class="slide-footer__page">Page 02</span><span class="slide-footer__band"></span><span class="slide-footer__accent"></span><span class="slide-footer__text">Talon Microsystems Confidential</span><span class="slide-footer__logo"><i></i>TALON</span></footer>
</section>

<section class="slide slide--work">
  <header class="slide-header"><span class="slide-header__line"></span><i class="slide-header__node"></i><h2 class="slide-header__title">What We Do</h2><i class="slide-header__node"></i><span class="slide-header__line"></span></header>
  <p class="column-text" style="top:100px">Sed ut perspiciatis unde omnis iste natus error sit voluptatem accusantium doloremque laudantium, totam rem aperiam, eaque ipsa quae ab illo inventore veritatis et quasi architecto beatae vitae dicta sunt explicabo. Nemo enim ipsam voluptatem quia voluptas sit aspernatur aut odit aut fugit, sed quia consequuntur magni dolores eos qui ratione voluptatem sequi nesciunt. Neque porro quisquam est, qui dolorem ipsum quia dolor sit amet, consectetur, adipisci velit, sed quia non numquam eius modi tempora incidunt ut labore et dolore magnam aliquam quaerat voluptatem.</p>
  <p class="column-text" style="top:328px">Sed ut perspiciatis unde omnis iste natus error sit voluptatem accusantium doloremque laudantium, totam rem aperiam, eaque ipsa quae ab illo inventore veritatis et quasi architecto beatae vitae dicta sunt explicabo. Nemo enim ipsam voluptatem quia voluptas sit aspernatur aut odit aut fugit, sed quia consequuntur magni dolores eos qui ratione voluptatem sequi nesciunt. Neque porro quisquam est, qui dolorem ipsum quia dolor sit amet, consectetur, adipisci velit, sed quia non numquam eius modi tempora incidunt ut labore et dolore magnam aliquam quaerat voluptatem.</p>
  <div class="photo-circle" role="img" aria-label="Photo of a technician in a cleanroom suit inspecting a circuit board"></div>
  <footer class="slide-footer"><span class="slide-footer__page">Page 03</span><span class="slide-footer__band"></span><span class="slide-footer__accent"></span><span class="slide-footer__text">Talon Microsystems Confidential</span><span class="slide-footer__logo"><i></i>TALON</span></footer>
</section>

<section class="slide slide--chart">
  <header class="slide-header"><span class="slide-header__line"></span><i class="slide-header__node"></i><h2 class="slide-header__title">Bar Chart</h2><i class="slide-header__node"></i><span class="slide-header__line"></span></header>
  <p class="column-text" style="top:100px">Sed ut perspiciatis unde omnis iste natus error sit voluptatem accusantium doloremque laudantium, totam rem aperiam, eaque ipsa quae ab illo inventore veritatis et quasi architecto beatae vitae dicta sunt explicabo. Nemo enim ipsam voluptatem quia voluptas sit aspernatur aut odit aut fugit, sed quia consequuntur magni dolores eos qui ratione voluptatem sequi nesciunt. Neque porro quisquam est, qui dolorem ipsum quia dolor sit amet, consectetur, adipisci velit, sed quia non numquam eius modi tempora incidunt ut labore et dolore magnam aliquam quaerat voluptatem.</p>
  <p class="column-text" style="top:328px">Sed ut perspiciatis unde omnis iste natus error sit voluptatem accusantium doloremque laudantium, totam rem aperiam, eaque ipsa quae ab illo inventore veritatis et quasi architecto beatae vitae dicta sunt explicabo. Nemo enim ipsam voluptatem quia voluptas sit aspernatur aut odit aut fugit, sed quia consequuntur magni dolores eos qui ratione voluptatem sequi nesciunt. Neque porro quisquam est, qui dolorem ipsum quia dolor sit amet, consectetur, adipisci velit, sed quia non numquam eius modi tempora incidunt ut labore et dolore magnam aliquam quaerat voluptatem.</p>
  <svg class="bar-chart" width="520" height="470" viewBox="0 0 520 470" font-family="Montserrat, sans-serif">
    <g font-size="17" font-weight="500" fill="#3a3a44">
      <text transform="translate(42 360) rotate(-90)">Aliquip ex ea Commodo</text>
      <text transform="translate(143 285) rotate(-90)">Aliquip ex ea</text>
      <text transform="translate(244 210) rotate(-90)">Excepteur sint</text>
      <text transform="translate(343 135) rotate(-90)">Neque porro</text>
      <text transform="translate(443 60) rotate(-90)">Porro</text>
    </g>
    <rect x="29" y="372" width="67" height="75" fill="var(--bar-1)"/>
    <polygon points="29,372 96,372 88,364 37,364" fill="#3f50a8"/>
    <rect x="130" y="296" width="67" height="151" fill="var(--bar-2)"/>
    <polygon points="130,296 197,296 189,288 138,288" fill="#3e47a6"/>
    <rect x="231" y="222" width="67" height="225" fill="var(--bar-3)"/>
    <polygon points="231,222 298,222 290,214 239,214" fill="#5140a8"/>
    <rect x="330" y="147" width="67" height="300" fill="var(--bar-4)"/>
    <polygon points="330,147 397,147 389,139 338,139" fill="#7a40a6"/>
    <rect x="430" y="75" width="67" height="372" fill="var(--bar-5)"/>
    <polygon points="430,75 497,75 489,67 438,67" fill="#ad3a90"/>
    <g font-size="20" font-weight="700" fill="#ffffff">
      <text transform="translate(70 438) rotate(-90)">20%</text>
      <text transform="translate(171 438) rotate(-90)">40%</text>
      <text transform="translate(272 438) rotate(-90)">60%</text>
      <text transform="translate(371 438) rotate(-90)">80%</text>
      <text transform="translate(471 438) rotate(-90)">100%</text>
    </g>
  </svg>
  <footer class="slide-footer"><span class="slide-footer__page">Page 04</span><span class="slide-footer__band"></span><span class="slide-footer__accent"></span><span class="slide-footer__text">Talon Microsystems Confidential</span><span class="slide-footer__logo"><i></i>TALON</span></footer>
</section>

<section class="slide slide--services">
  <header class="slide-header"><span class="slide-header__line"></span><i class="slide-header__node"></i><h2 class="slide-header__title">Our Services</h2><i class="slide-header__node"></i><span class="slide-header__line"></span></header>

  <div class="service" style="left:36px; top:95px">
    <div class="service__head"><svg class="service__tick" width="16" height="16" viewBox="0 0 16 16"><circle cx="8" cy="8" r="6.5" fill="none" stroke="var(--brand)" stroke-width="2"/><path d="M5 8.2l2 2 4-4" fill="none" stroke="var(--brand)" stroke-width="2"/></svg><span>Sed ut perspiciatis unde omnis iste natus error sit voluptatem accusantium doloremque laudantium</span></div>
    <div class="service__sub"><i class="service__ring"></i><span>Duis aute irure dolor in reprehenderit in voluptate velit esse cillum dolore reprehenderit in voluptate velit esse</span></div>
    <div class="service__sub"><i class="service__ring"></i><span>Duis aute irure dolor in reprehenderit in voluptate velit esse cillum dolore reprehenderit in voluptate velit esse</span></div>
  </div>
  <div class="service" style="left:603px; top:95px">
    <div class="service__head"><svg class="service__tick" width="16" height="16" viewBox="0 0 16 16"><circle cx="8" cy="8" r="6.5" fill="none" stroke="var(--brand)" stroke-width="2"/><path d="M5 8.2l2 2 4-4" fill="none" stroke="var(--brand)" stroke-width="2"/></svg><span>Sed ut perspiciatis unde omnis iste natus error sit voluptatem accusantium doloremque laudantium</span></div>
    <div class="service__sub"><i class="service__ring"></i><span>Duis aute irure dolor in reprehenderit in voluptate velit esse cillum dolore reprehenderit in voluptate velit esse</span></div>
    <div class="service__sub"><i class="service__ring"></i><span>Duis aute irure dolor in reprehenderit in voluptate velit esse cillum dolore reprehenderit in voluptate velit esse</span></div>
  </div>
  <div class="service" style="left:36px; top:276px">
    <div class="service__head"><svg class="service__tick" width="16" height="16" viewBox="0 0 16 16"><circle cx="8" cy="8" r="6.5" fill="none" stroke="var(--brand)" stroke-width="2"/><path d="M5 8.2l2 2 4-4" fill="none" stroke="var(--brand)" stroke-width="2"/></svg><span>Sed ut perspiciatis unde omnis iste natus error sit voluptatem accusantium doloremque laudantium</span></div>
    <div class="service__sub"><i class="service__ring"></i><span>Duis aute irure dolor in reprehenderit in voluptate velit esse cillum dolore reprehenderit in voluptate velit esse</span></div>
    <div class="service__sub"><i class="service__ring"></i><span>Duis aute irure dolor in reprehenderit in voluptate velit esse cillum dolore reprehenderit in voluptate velit esse</span></div>
  </div>
  <div class="service" style="left:603px; top:276px">
    <div class="service__head"><svg class="service__tick" width="16" height="16" viewBox="0 0 16 16"><circle cx="8" cy="8" r="6.5" fill="none" stroke="var(--brand)" stroke-width="2"/><path d="M5 8.2l2 2 4-4" fill="none" stroke="var(--brand)" stroke-width="2"/></svg><span>Sed ut perspiciatis unde omnis iste natus error sit voluptatem accusantium doloremque laudantium</span></div>
    <div class="service__sub"><i class="service__ring"></i><span>Duis aute irure dolor in reprehenderit in voluptate velit esse cillum dolore reprehenderit in voluptate velit esse</span></div>
    <div class="service__sub"><i class="service__ring"></i><span>Duis aute irure dolor in reprehenderit in voluptate velit esse cillum dolore reprehenderit in voluptate velit esse</span></div>
  </div>
  <div class="service" style="left:36px; top:452px">
    <div class="service__head"><svg class="service__tick" width="16" height="16" viewBox="0 0 16 16"><circle cx="8" cy="8" r="6.5" fill="none" stroke="var(--brand)" stroke-width="2"/><path d="M5 8.2l2 2 4-4" fill="none" stroke="var(--brand)" stroke-width="2"/></svg><span>Sed ut perspiciatis unde omnis iste natus error sit voluptatem accusantium doloremque laudantium</span></div>
    <div class="service__sub"><i class="service__ring"></i><span>Duis aute irure dolor in reprehenderit in voluptate velit esse cillum dolore reprehenderit in voluptate velit esse</span></div>
  </div>
  <div class="service" style="left:603px; top:452px">
    <div class="service__head"><svg class="service__tick" width="16" height="16" viewBox="0 0 16 16"><circle cx="8" cy="8" r="6.5" fill="none" stroke="var(--brand)" stroke-width="2"/><path d="M5 8.2l2 2 4-4" fill="none" stroke="var(--brand)" stroke-width="2"/></svg><span>Sed ut perspiciatis unde omnis iste natus error sit voluptatem accusantium doloremque laudantium</span></div>
    <div class="service__sub"><i class="service__ring"></i><span>Duis aute irure dolor in reprehenderit in voluptate velit esse cillum dolore reprehenderit in voluptate velit esse</span></div>
  </div>

  <footer class="slide-footer"><span class="slide-footer__page">Page 05</span><span class="slide-footer__band"></span><span class="slide-footer__accent"></span><span class="slide-footer__text">Talon Microsystems Confidential</span><span class="slide-footer__logo"><i></i>TALON</span></footer>
</section>

<section class="slide slide--closing">
  <div class="brand-mark"><i class="brand-mark__dot"></i><span class="brand-mark__name">Talon Microsystems</span></div>
</section>

</body>
</html>
```